Verdant Systems Business Card

want the back of card to be blue- with the logo in the center
front of card- info plus logo (info being mailing address, email address, and website address )
4 different names with titles to have on cards
1) Calvin Borsted - Owner
2) Naomi Trelvik- Customer Relationship Specialist
3) Felix Andrade- Vice President of Sales
4) Owen Markby- Chief Technology Officer

Target Market(s)

tech company in the government/probation office industry

Industry/Entity Type

Government Office

Contact Information for Business Card

1) Calvin Borsted - Owner

Colors
0355a3
ffffff

Requirements
Must have
• back side should be blue, with the logo placed in the center
• front side needs to include both the logo, as well as company info (info should include website address, email address, and mailing address)

```html
<!DOCTYPE html>
<html lang="en">
<head>
<meta charset="utf-8">
<title>Verdant Systems Business Card</title>
<link rel="stylesheet" href="https://fonts.googleapis.com/css2?family=Crimson+Pro:wght@600&family=Roboto:wght@400;500&display=swap">
<style>
  :root {
    --navy: #172b52;
    --white: #ffffff;
    --backdrop: #e8e5e0;
    --shadow: rgba(0, 0, 0, 0.28);
  }
  * { margin: 0; padding: 0; box-sizing: border-box; }
  html, body {
    width: 1125px;
    height: 1200px;
    overflow: hidden;
    background: var(--backdrop);
  }
  .canvas { position: relative; width: 1125px; height: 1200px; }
  .card {
    position: absolute;
    left: 166px;
    width: 800px;
    height: 456px;
    background: var(--navy);
    color: var(--white);
    box-shadow: 0 3px 10px var(--shadow);
    overflow: hidden;
  }
  .card--front { top: 103px; }
  .card--back { top: 620px; }

  .wordmark {
    font-family: "Crimson Pro", Georgia, serif;
    font-weight: 600;
    color: var(--white);
    white-space: nowrap;
    letter-spacing: 0.02em;
  }
  .card--front .wordmark {
    position: absolute;
    left: 52px;
    top: 66px;
    font-size: 36px;
    line-height: 1;
  }

  .brand-panel {
    position: absolute;
    left: 370px;
    top: 0;
    width: 430px;
    height: 456px;
    background: var(--white);
    display: flex;
    align-items: center;
    justify-content: center;
  }
  .brand-panel__name {
    font-family: "Crimson Pro", Georgia, serif;
    font-weight: 600;
    font-size: 52px;
    line-height: 1.05;
    color: var(--navy);
    text-align: center;
    letter-spacing: 0.02em;
  }

  .holder { position: absolute; left: 53px; top: 222px; }
  .holder__name {
    font-family: "Crimson Pro", Georgia, serif;
    font-weight: 600;
    font-size: 33px;
    line-height: 1;
  }
  .holder__title {
    font-family: "Roboto", Arial, sans-serif;
    font-weight: 500;
    font-size: 19px;
    margin-top: 4px;
  }

  .contact {
    position: absolute;
    left: 51px;
    top: 296px;
    list-style: none;
    font-family: "Roboto", Arial, sans-serif;
    font-size: 18px;
  }
  .contact__item {
    display: flex;
    align-items: center;
    height: 25.7px;
    white-space: nowrap;
  }
  .contact__icon { width: 16px; height: 16px; margin-right: 13px; flex: none; fill: var(--white); }

  .card--back .wordmark {
    position: absolute;
    left: 0;
    right: 0;
    top: 218px;
    text-align: center;
    font-size: 58px;
    line-height: 1;
  }
  .back__url {
    position: absolute;
    left: 0;
    right: 0;
    top: 392px;
    text-align: center;
    font-family: "Roboto", Arial, sans-serif;
    font-size: 19px;
    letter-spacing: 0.16em;
  }
</style>
</head>
<body>
<main class="canvas">
  <section class="card card--front" aria-label="Card front">
    <div class="wordmark">Verdant Systems</div>

    <div class="brand-panel">
      <div class="brand-panel__name">Verdant<br>Systems</div>
    </div>

    <div class="holder">
      <div class="holder__name">Calvin Borsted</div>
      <div class="holder__title">Owner</div>
    </div>

    <ul class="contact">
      <li class="contact__item">
        <svg class="contact__icon" viewBox="0 0 16 16" aria-hidden="true"><path d="M3.2 1l2.4 2.6-1.4 2a9 9 0 0 0 6.2 6.2l2-1.4L15 13l-1.8 2C6.8 15 1 9.2 1 2.8z"/></svg>
        <span>369-555-0142</span>
      </li>
      <li class="contact__item">
        <svg class="contact__icon" viewBox="0 0 16 16" aria-hidden="true"><path d="M4 0h8a1 1 0 0 1 1 1v14a1 1 0 0 1-1 1H4a1 1 0 0 1-1-1V1a1 1 0 0 1 1-1zm1 2v10h6V2zm3 11a1 1 0 1 0 0 2 1 1 0 0 0 0-2z"/></svg>
        <span>369-555-0187</span>
      </li>
      <li class="contact__item">
        <svg class="contact__icon" viewBox="0 0 16 16" aria-hidden="true"><path d="M1 3.5h14v9H1zm1.4 1.2L8 9l5.6-4.3v-.1H2.4zM2 11.5h12V5.9L8 10.4 2 5.9z"/></svg>
        <span>hello@verdantsystems.com</span>
      </li>
      <li class="contact__item">
        <svg class="contact__icon" viewBox="0 0 16 16" aria-hidden="true"><circle cx="8" cy="8" r="7.5"/><path d="M4 4.5l2.5.5 1 2-1.5 1.5.5 3L5 10 3.5 7zM10 3l2 1.5-.5 2.5-2-.5z" fill="#172b52"/></svg>
        <span>www.verdantsystems.com</span>
      </li>
      <li class="contact__item">
        <svg class="contact__icon" viewBox="0 0 16 16" aria-hidden="true"><path d="M8 0a5.5 5.5 0 0 0-5.5 5.5C2.5 10 8 16 8 16s5.5-6 5.5-10.5A5.5 5.5 0 0 0 8 0zm0 7.8a2.3 2.3 0 1 1 0-4.6 2.3 2.3 0 0 1 0 4.6z"/></svg>
        <span>14 Harlow Ave, Helena MT</span>
      </li>
    </ul>
  </section>

  <section class="card card--back" aria-label="Card back">
    <div class="wordmark">Verdant Systems</div>
    <div class="back__url">www.verdantsystems.com</div>
  </section>
</main>
</body>
</html>
```